Tech business card design

We need an amazing business card design for our new business 'Pexla' a marketing tech startup based in Sydney, Australia. We provide an online marketplace for businesses to search and buy advertising media, connect with service providers and learn more about marketing. We wish to communicate 'cool tech', reliability and professionalism and design based around our logo.

Target Market(s)

Business Owners

Contact Information for Business Card

Name
Position
Email Address
Website
Phone Number

Font styles to use
Other font styles liked:
• Avenir & Avenir Next

Colors

Designer to choose colors to be used in the design.

```html
<!DOCTYPE html>
<html lang="en">
<head>
<meta charset="utf-8">
<title>Pexla Business Card</title>
<link href="https://fonts.googleapis.com/css2?family=Mulish:wght@400;700;800;900&display=swap" rel="stylesheet">
<style>
  :root {
    --backdrop: #94a9b4;
    --navy: #25284a;
    --ink: #231f20;
    --paper: #ffffff;
    --card-edge: #d7dde0;
  }
  * { margin: 0; padding: 0; box-sizing: border-box; }
  html, body { width: 1079px; height: 1200px; overflow: hidden; }
  body {
    background: var(--backdrop);
    font-family: "Mulish", "Avenir Next", Avenir, sans-serif;
    position: relative;
  }
  .card {
    position: absolute;
    left: 87px;
    width: 904px;
    height: 516px;
    background: var(--paper);
    border-radius: 26px;
    border: 1px solid var(--card-edge);
    overflow: hidden;
  }
  .card--front { top: 50px; }
  .card--back { top: 636px; }

  .holder { position: absolute; left: 68px; top: 56px; color: var(--ink); }
  .holder__name { font-size: 30px; font-weight: 800; letter-spacing: 0.2px; line-height: 1.1; }
  .holder__role { font-size: 26px; font-weight: 400; line-height: 1.3; }

  .brand-name {
    position: absolute;
    font-weight: 900;
    letter-spacing: -2px;
    line-height: 1;
  }
  .card--front .brand-name { right: 78px; top: 30px; font-size: 128px; color: var(--navy); }

  .contact-band {
    position: absolute;
    left: 0; top: 253px;
    width: 100%; height: 226px;
    background: var(--navy);
    color: var(--paper);
  }
  .contact-list { position: absolute; left: 67px; top: 44px; list-style: none; }
  .contact-list li {
    display: flex; align-items: center; gap: 9px;
    font-size: 24px; height: 38px;
  }
  .contact-list svg { width: 23px; height: 23px; flex: none; }
  .contact-list .web { letter-spacing: 2.5px; }
  .address {
    position: absolute; right: 53px; top: 64px;
    text-align: right; font-size: 24px; line-height: 30px;
  }

  .back-panel {
    position: absolute; inset: 17px;
    background: var(--navy);
    border-radius: 30px;
  }
  .card--back .brand-name {
    left: 0; right: 0; top: 272px;
    text-align: center; font-size: 128px; color: var(--paper);
  }
  .back-site {
    position: absolute; left: 0; right: 0; top: 422px;
    text-align: center; color: var(--paper);
    font-size: 30px; letter-spacing: 4px;
  }
</style>
</head>
<body>
  <section class="card card--front">
    <div class="holder">
      <p class="holder__name">JOHN SMITH</p>
      <p class="holder__role">Position</p>
    </div>
    <p class="brand-name">pexla</p>
    <div class="contact-band">
      <ul class="contact-list">
        <li>
          <svg viewBox="0 0 24 24" aria-hidden="true"><circle cx="12" cy="12" r="10.5" fill="none" stroke="#fff" stroke-width="1.6"/><path d="M9 6.5c-1.5 1-2 2.6-1.4 4.6.8 2.6 2.6 5 4.6 6.4 1.2.8 2.6.8 3.6-.2l-1.8-2.2-1.4.6c-1.3-1-2.3-2.4-2.8-4l1.2-1z" fill="#fff"/></svg>
          <span>012-345-6789</span>
        </li>
        <li>
          <svg viewBox="0 0 24 24" aria-hidden="true"><rect x="1" y="5" width="22" height="14" fill="#fff"/><path d="M1 5l11 8 11-8M1 19l8-7M23 19l-8-7" fill="none" stroke="#25284a" stroke-width="1.6"/></svg>
          <span>info@pexla.com</span>
        </li>
        <li>
          <svg viewBox="0 0 24 24" aria-hidden="true" fill="none" stroke="#fff" stroke-width="1.5"><circle cx="12" cy="12" r="10.5"/><ellipse cx="12" cy="12" rx="4.5" ry="10.5"/><path d="M1.5 12h21M3 7h18M3 17h18M12 1.5v21"/></svg>
          <span class="web">www.pexla.com</span>
        </li>
      </ul>
      <p class="address">Street name City Name,<br>Zipcode,012345</p>
    </div>
  </section>

  <section class="card card--back">
    <div class="back-panel">
      <p class="brand-name">pexla</p>
      <p class="back-site">www.pexla.com</p>
    </div>
  </section>
</body>
</html>
```